Teeth Whitening Clinic Website Redesign - Social Proof Theme

NEW TEETH SITEREVAMP CURRENT WEBSITE:WWW.SANDIEGOSTEETHWHITENING.COMTHEME:SOCIAL PROOF/5 STAR REVIEWS/TESTIMONIALS THEME:https://maps.example.net/QxRvPLoKzN84 I want a testimonial themed, social proof themed website so customers will be sold by testimonials all over the website….I like a nice clean simple site but with all important factors standing out like CALLS TO ACTIONS, for example the $99 special link in header on original design. Also, testimonials throughout the website placed methodically as not to be FORCED and CLUTTEREDKeep all same exact content for all pages and elements of current design. All buttons, calls to action, navigation, etc. Please do not leave anything out from current design. SPECIAL INSTRUCTIONS for banner image:I want to use actual customer photos inside the banner image in a way that really pops and grabs attention. Please grab some customer photos from my PG Account, fk or rateway account: Also, I want to integrate 5 star rateway logo, friendbook review 5 stars icon, searchly business page 5 stars icon, etc. on the banner as well to show social proof as much as possible. Actual customer photos to be used throughout website:https://www.photogram.example/brightharborsmilestudioplace/ https://www.friendbook.com/SDTeethWhitening/https://www.reviewhub.example/biz/bright-harbor-smile-studio-place-bright-harbor-5 Reviews:https://www.reviewhub.example/biz/bright-harbor-smile-studio-place-bright-harbor-5 https://www.friendbook.com/pg/SDTeethWhitening/reviews/?ref=page_internalhttps://goo.gl/maps/TmJcABLAJwC2 Please do home page first to come up with theme then after approval home page we can move forward additional pages.

Target Market(s)

PEOPLE THAT CARE ABOUT DENTAL HYGEINE AND OR CARE ABOUT THEIR TEETH SMILE

Industry/Entity Type

Dental Clinic

Number of Pages Required

5+ page

Colors

Designer to choose colors to be used in the design.

Requirements
Must have
• NEW TEETH SITE
• REVAMP CURRENT WEBSITE:
• WWW.BRIGHTHARBORSMILESTUDIO.EXAMPLE
• THEME:
• SOCIAL PROOF/5 STAR REVIEWS/TESTIMONIALS THEME:
• https://maps.example.net/QxRvPLoKzN84
• I want a testimonial themed, social proof themed website so customers will be sold by testimonials all over the website….I like a nice clean simple site but with all important factors standing out like CALLS TO ACTIONS, for example the $99 special link in header on original design. Also, testimonials throughout the website placed methodically as not to be FORCED and CLUTTERED
• Keep all same exact content for all pages and elements of current design. All buttons, calls to action, navigation, etc. Please do not leave anything out from current design.
• SPECIAL INSTRUCTIONS for banner image:
• I want to use actual customer photos inside the banner image in a way that really pops and grabs attention. Please grab some customer photos from my PG Account, fk or rateway account:
• Also, I want to integrate 5 star rateway logo, friendbook review 5 stars icon, searchly business page 5 stars icon, etc. on the banner as well to show social proof as much as possible.
• Actual customer photos to be used throughout website:
• https://www.photogram.example/brightharborsmilestudioplace/
• https://www.friendbook.example/BHSmileStudio/
• https://www.reviewhub.example/biz/bright-harbor-smile-studio-place-bright-harbor-5
• Reviews:
• https://www.friendbook.example/pg/BHSmileStudio/reviews/?ref=page_internal
• Please do home page first to come up with theme then after approval home page we can move forward additional pages.
Nice to have
• NEW TEETH SITE
• REVAMP CURRENT WEBSITE:
• THEME:
• Reviews:
Should not have
• NEW TEETH SITE
• REVAMP CURRENT WEBSITE:
• THEME:
• Reviews:

```html
<!DOCTYPE html>
<html lang="en">
<head>
<meta charset="utf-8">
<title>Bright Harbor Smile Studio</title>
<link rel="stylesheet" href="https://fonts.googleapis.com/css2?family=Poppins:wght@400;500;600&family=Rubik:wght@500;600&family=Roboto:ital,wght@0,400;0,500;0,700;1,400;1,700&display=swap">
<style>
:root{
  --cyan:#1ab8e4;
  --cyan-deep:#0fa9d6;
  --teal:#3aa9c0;
  --navy:#2c5a8c;
  --ink:#111;
  --muted:#666;
  --grey-bg:#f0f0f0;
  --row-line:#dcdcdc;
  --star:#f7b500;
  --orange-star:#f08a1c;
}
*{margin:0;padding:0;box-sizing:border-box}
html,body{width:1200px;height:4142px;overflow:hidden;background:#fff}
body{font-family:"Roboto",sans-serif;color:var(--ink);position:relative}
section,header,footer,.topbar{position:relative;width:1200px}
.abs{position:absolute}

.topbar{height:42px;background:var(--cyan);color:#fff;font-size:15px}
.topbar .addr{left:100px;top:11px;display:flex;align-items:center;gap:10px}
.topbar .deal{left:688px;top:11px;display:flex;align-items:center;gap:10px}

.nav{height:87px;background:#fff}
.brand{display:flex;align-items:center;gap:8px}
.brand .mark{border-radius:50%;background:#e3e9ee;border:2px solid #c7d3dc}
.brand .name{font-family:"Poppins",sans-serif;color:#555;line-height:1.05}
.nav .brand{left:88px;top:14px}
.nav .brand .mark{width:56px;height:56px}
.nav .brand .name{font-size:18px}
.nav ul{list-style:none;display:flex;gap:16px;left:336px;top:32px;font-family:"Poppins",sans-serif;font-size:15px;color:#333}
.nav li.active{color:var(--cyan);font-weight:600}

.hero{height:582px;overflow:hidden}
.hero .photo{inset:0;background:linear-gradient(120deg,#3a4a58 0%,#6a7280 35%,#555d6b 60%,#394452 100%)}
.hero .shade{inset:0;background:rgba(10,20,35,.35)}
.hero h1{width:1200px;top:132px;text-align:center;color:#fff;font-family:"Poppins",sans-serif;font-weight:500;font-size:52px;line-height:55px}
.hero .sub{width:1200px;top:278px;text-align:center;color:#fff;font-weight:700;font-size:17px}
.btn{display:inline-block;font-size:16px;padding:0 18px;line-height:46px;height:46px}
.hero .book{left:434px;top:350px;background:var(--cyan);color:#111}
.hero .contact{left:605px;top:350px;background:#fff;color:#111}
.proof{left:0;top:474px;width:1200px;height:108px;background:rgba(20,30,45,.55)}
.proof .item{top:0;width:300px;height:108px;text-align:center;color:#fff}
.proof .label{font-family:"Poppins",sans-serif;font-weight:600;font-size:42px;margin-top:14px;line-height:50px}
.proof .stars{color:var(--star);font-size:24px;letter-spacing:2px;line-height:28px}

.about{height:527px}
.video{left:106px;top:118px;width:322px;height:322px;border-radius:50%;background:linear-gradient(160deg,#8ab4c2,#4a6f88 60%,#6d5aa0);border:3px solid #5aa7b4}
.play{left:56px;width:64px;height:64px}
.about h2{left:481px;top:106px;font-family:"Rubik",sans-serif;font-weight:600;color:var(--cyan);font-size:31px}
.about h3{left:481px;top:163px;font-size:20px;font-weight:700}
.about p{left:481px;top:214px;width:620px;font-size:16px;line-height:27px;color:#222}
.about .cta{left:482px;top:401px;background:var(--cyan);color:#fff;padding:0 32px}

.how{height:556px;overflow:hidden}
.how .photo{inset:0;background:linear-gradient(110deg,#2cc0e6 0%,#38c3e8 45%,#5fb6d6 70%,#38bde4 100%)}
.how h2{width:1200px;top:104px;text-align:center;color:#fff;font-family:"Rubik",sans-serif;font-weight:600;font-size:36px}
.how p{left:120px;width:960px;top:208px;text-align:center;color:#fff;font-weight:500;font-size:17px;line-height:32px}
.how .more{left:533px;top:382px;background:#fff;color:#111;padding:0 24px}

.why{height:820px}
.why h2{width:1200px;top:70px;text-align:center;font-family:"Rubik",sans-serif;font-weight:600;color:var(--cyan);font-size:36px}
.why svg{left:0;top:0}
.why .lbl{font-size:22px;font-weight:500;color:#111}
.center-photo{left:430px;top:292px;width:320px;height:320px;border-radius:50%;background:linear-gradient(160deg,#eef0f2,#7a6aa8 60%,#333 100%)}

.compare{height:611px;background:var(--grey-bg)}
.compare h2{width:1200px;top:84px;text-align:center;font-family:"Rubik",sans-serif;font-weight:600;color:var(--cyan);font-size:36px}
.table{left:98px;top:199px;width:1002px;height:316px;background:#e4e4e4}
.col{position:absolute;top:0;height:316px}
.col .head{height:67px;background:var(--navy);color:#fff;display:flex;align-items:center;justify-content:center;font-family:"Roboto",sans-serif;font-weight:700;font-size:24px}
.col .cell{height:42px;border-bottom:1px solid var(--row-line);display:flex;align-items:center;justify-content:center;font-size:14px;color:#666;background:#f2f2f2}
.col.first .head{font-size:20px;justify-content:flex-start;padding-left:55px;line-height:24px}
.col.first .cell{color:#222}
.col.hl{top:-17px;height:341px;background:var(--cyan-deep);box-shadow:0 0 14px rgba(0,0,0,.2)}
.col.hl .head{height:84px;background:#fff;color:#555;font-family:"Poppins",sans-serif;font-weight:500;font-size:17px;gap:8px}
.col.hl .cell{background:var(--cyan-deep);color:#fff;font-weight:500;border-bottom:1px solid rgba(255,255,255,.35)}

.reviews{height:523px}
.reviews h2{width:1200px;top:66px;text-align:center;font-family:"Poppins",sans-serif;font-weight:600;color:var(--cyan);font-size:37px}
.avatar{width:122px;height:122px;border-radius:50%;background:linear-gradient(160deg,#e8e8e8,#b9b2aa);border:2px solid #444}
.quote{font-style:italic;font-size:16px;line-height:27px;color:#333}
.who{font-style:italic;font-weight:700;font-size:19px}
.rstars{color:var(--orange-star);font-size:24px;letter-spacing:4px}
.divider{left:597px;top:180px;width:1px;height:220px;background:#ccc}
.dots{left:586px;top:464px;display:flex;gap:4px}
.dots span{width:8px;height:8px;border-radius:50%;background:#222}
.dots span.on{background:var(--cyan)}

.foot{height:394px}
.foot .brand{left:88px;top:140px}
.foot .brand .mark{width:100px;height:100px}
.foot .brand .name{font-size:34px}
.foot h4{font-family:"Poppins",sans-serif;font-weight:600;font-size:25px}
.foot ul{list-style:none;font-size:17px;line-height:29px;color:#222}
.foot .news p{font-size:17px;line-height:32px}
.foot input{width:206px;height:37px;border:1px solid #555;font-size:12px;padding-left:6px;font-family:"Roboto",sans-serif}
.foot .submit{background:#000;color:#fff;font-size:16px;width:107px;height:36px;line-height:36px;text-align:center}
.copy{width:1200px;top:352px;text-align:center;font-size:16px;color:#333}
</style>
</head>
<body>

<div class="topbar">
  <div class="abs addr">
    <svg width="22" height="24" viewBox="0 0 22 24"><path d="M11 2a7 7 0 0 0-7 7c0 5 7 12 7 12s7-7 7-12a7 7 0 0 0-7-7z" fill="none" stroke="#fff" stroke-width="1.6"/><circle cx="11" cy="9" r="2.5" fill="none" stroke="#fff" stroke-width="1.6"/></svg>
    4470 Harbor View Rd. #118 Bright Harbor, CA 90210
  </div>
  <div class="abs deal">
    <svg width="26" height="26" viewBox="0 0 26 26"><circle cx="13" cy="13" r="11" fill="none" stroke="#fff" stroke-width="1.8"/><text x="13" y="18" text-anchor="middle" fill="#fff" font-size="14" font-family="Roboto" font-weight="700">$</text></svg>
    Click Here to Get Our $99 Teeth Whiting Deal (Reg: $378)
  </div>
</div>

<header class="nav">
  <div class="abs brand">
    <div class="mark"></div>
    <div class="name">BRIGHT HARBOR<br><span style="font-size:12px;color:var(--teal)">Smile Studio</span></div>
  </div>
  <ul class="abs">
    <li class="active">Home</li><li>Our Process</li><li>Photos</li><li>Free Treatments</li><li>Testimonials</li><li>Blog</li><li>FAQ</li><li>Contact</li><li>Gift Certificates</li>
  </ul>
</header>

<section class="hero">
  <div class="abs photo" role="img" aria-label="Collage of smiling clinic customers and staff holding review signs"></div>
  <div class="abs shade"></div>
  <h1 class="abs">Get That White Smile You’ve<br>Always Wanted</h1>
  <div class="abs sub">Amazing Results, The Most Effective System, More Affordable Than The Dentist</div>
  <a class="abs btn book">Book Online</a>
  <a class="abs btn contact">Contact us</a>
  <div class="abs proof">
    <div class="abs item" style="left:80px"><div class="label">friendbook</div><div class="stars">★★★★★</div></div>
    <div class="abs item" style="left:415px"><div class="label">searchly</div><div class="stars">★★★★★</div></div>
    <div class="abs item" style="left:818px"><div class="label">rateway</div><div class="stars">★★★★★</div></div>
  </div>
</section>

<section class="about">
  <div class="abs video" role="img" aria-label="Video still of a clinic staff member in front of the studio wall">
    <svg class="abs play" style="left:126px;top:126px" viewBox="0 0 64 64"><circle cx="32" cy="32" r="29" fill="none" stroke="#fff" stroke-width="4"/><path d="M25 19 L46 32 L25 45 Z" fill="#fff"/></svg>
  </div>
  <h2 class="abs">BRIGHT HARBOR SMILE STUDIO</h2>
  <h3 class="abs">The best price, service and results.</h3>
  <p class="abs">Bright Harbor Smile Studio features state-of-the-art technologies that are safe, industry-unique and very cost-effective. Our teeth whitening system utilizes the latest blue light whitening technology. Our Blue Light Systems are calibrated precisely for optimal activation of our exclusive hydrogen peroxide based whitening solution which is manufactured in a FDA registered facility in the USA.</p>
  <a class="abs btn cta">Book Appointment Online</a>
</section>

<section class="how">
  <div class="abs photo" role="img" aria-label="Close-up of a patient smiling during a whitening treatment, tinted blue"></div>
  <h2 class="abs">HOW IT WORKS</h2>
  <p class="abs">We have a very effective teeth whitening treatment that is guaranteed to get you quick results in about 1 hour. To start the treatment you’ll apply a Hydrogen Peroxide based whitening agent to your teeth. We then place our cold blue light directly in front of your exposed teeth for 15 minutes per treatment. The lighting systems we use activate the whitening agent and thats what accelerates the whitening process, giving you whiter teeth in less than an hour.</p>
  <a class="abs btn more">Read More</a>
</section>

<section class="why">
  <h2 class="abs">WHY CHOOSE US</h2>
  <svg class="abs" width="1200" height="820" viewBox="0 0 1200 820">
    <g stroke="#6b8fb8" stroke-width="1.5" fill="none">
      <line x1="362" y1="223" x2="473" y2="338"/>
      <line x1="830" y1="223" x2="712" y2="345"/>
      <line x1="256" y1="451" x2="423" y2="451"/>
      <line x1="922" y1="451" x2="755" y2="451"/>
      <line x1="362" y1="682" x2="473" y2="570"/>
      <line x1="819" y1="682" x2="706" y2="570"/>
    </g>
    <circle cx="590" cy="452" r="163" fill="none" stroke="#222" stroke-width="2" stroke-dasharray="6 5"/>
    <g fill="#fff" stroke="#4a7ab0" stroke-width="2">
      <circle cx="473" cy="338" r="8"/><circle cx="712" cy="345" r="8"/>
      <circle cx="423" cy="451" r="8"/><circle cx="755" cy="451" r="8"/>
      <circle cx="473" cy="570" r="8"/><circle cx="706" cy="570" r="8"/>
    </g>
    <g fill="var(--cyan)">
      <circle cx="362" cy="223" r="40"/><circle cx="830" cy="223" r="40"/>
      <circle cx="256" cy="451" r="40"/><circle cx="922" cy="451" r="40"/>
      <circle cx="362" cy="682" r="40"/><circle cx="819" cy="682" r="40"/>
    </g>
    <g fill="none" stroke="#fff" stroke-width="2.4" stroke-linecap="round" stroke-linejoin="round">
      <rect x="355" y="200" width="14" height="46" rx="5"/><line x1="362" y1="212" x2="362" y2="232"/>
      <path d="M820 212 L840 212 L846 238 L814 238 Z"/><text x="830" y="234" text-anchor="middle" fill="#fff" stroke="none" font-size="18" font-family="Roboto" font-weight="700">$</text>
      <path d="M242 436 C242 428 252 430 256 434 C260 430 270 428 270 436 C270 448 264 468 261 468 C258 468 258 454 256 454 C254 454 254 468 251 468 C248 468 242 448 242 436 Z"/>
      <circle cx="928" cy="444" r="11"/><line x1="936" y1="452" x2="946" y2="462"/><rect x="902" y="450" width="14" height="18"/>
      <path d="M348 672 C348 664 358 666 362 670 C366 666 376 664 376 672 C376 684 370 702 367 702 C364 702 364 690 362 690 C360 690 360 702 357 702 C354 702 348 684 348 672 Z"/>
      <rect x="803" y="664" width="32" height="8" rx="2"/><path d="M805 678 C805 676 811 676 813 678 C815 676 823 676 825 678 C827 676 833 676 833 678 L830 700 L808 700 Z"/>
    </g>
  </svg>
  <div class="abs center-photo" role="img" aria-label="Photo of two smiling clinic team members"></div>
  <div class="abs lbl" style="left:230px;top:206px">Dentist</div>
  <div class="abs lbl" style="left:912px;top:208px">Price</div>
  <div class="abs lbl" style="left:108px;top:440px">Services</div>
  <div class="abs lbl" style="left:995px;top:444px">Results</div>
  <div class="abs lbl" style="left:196px;top:676px">No Pain</div>
  <div class="abs lbl" style="left:881px;top:674px">Convenience</div>
</section>

<section class="compare">
  <h2 class="abs">COMPARE US</h2>
  <div class="abs table">
    <div class="col first" style="left:0;width:200px">
      <div class="head">Package<br>Features</div>
      <div class="cell">Speed</div><div class="cell">Ease of Use</div><div class="cell">Cost</div><div class="cell">Availability</div><div class="cell">Pain</div>
    </div>
    <div class="col" style="left:200px;width:193px">
      <div class="head">GLOWPRO</div>
      <div class="cell">1-2 Hours</div><div class="cell">Difficult / Dentist</div><div class="cell">$300 - $600</div><div class="cell">Limited Availability</div><div class="cell">Pain &amp; Sensitivity</div>
    </div>
    <div class="col" style="left:590px;width:198px">
      <div class="head">LUMASMILE</div>
      <div class="cell">7-14 Days</div><div class="cell">Difficult / Dentist</div><div class="cell">$300 - $600</div><div class="cell">Limited Availability</div><div class="cell">Sensitivity</div>
    </div>
    <div class="col" style="left:788px;width:214px">
      <div class="head">HOME KITS</div>
      <div class="cell">7-30 Days</div><div class="cell">Difficult</div><div class="cell">$50 - $150</div><div class="cell">Store Purchase</div><div class="cell">Sensitivity</div>
    </div>
    <div class="col hl" style="left:393px;width:197px">
      <div class="head"><span style="width:30px;height:30px;border-radius:50%;background:#e3e9ee;border:2px solid #c7d3dc"></span>BRIGHT HARBOR</div>
      <div class="cell">45 Mins</div><div class="cell">Very Easy</div><div class="cell">$378</div><div class="cell">Appt Only</div><div class="cell">No Pain</div>
    </div>
  </div>
</section>

<section class="reviews">
  <h2 class="abs">What Our Happy Clients Say About Us</h2>
  <div class="abs avatar" style="left:108px;top:210px" role="img" aria-label="Portrait of a happy client"></div>
  <div class="abs quote" style="left:252px;top:216px;width:336px">“<br>I The staff is really friendly and welcoming and Marisol did such a good job with my smile!. ”</div>
  <div class="abs who" style="left:253px;top:340px">Dana K, New York</div>
  <div class="abs rstars" style="left:253px;top:372px">★★★★★</div>
  <div class="abs divider"></div>
  <div class="abs quote" style="left:622px;top:216px;width:340px">“<br>I also appreciated that they took the time to explain all the instructions and didn't mind me asking addition l questions about the take home kit and aftercare ”</div>
  <div class="abs who" style="left:641px;top:342px">Owen Tallis, New York</div>
  <div class="abs rstars" style="left:641px;top:374px">★★★★★</div>
  <div class="abs avatar" style="left:975px;top:210px" role="img" aria-label="Portrait of a happy client"></div>
  <div class="abs dots"><span></span><span class="on"></span><span></span></div>
</section>

<footer class="foot">
  <div class="abs brand">
    <div class="mark"></div>
    <div class="name">BRIGHT HARBOR<br><span style="font-size:21px;color:var(--teal)">Smile Studio</span></div>
  </div>
  <h4 class="abs" style="left:515px;top:50px">QUICK LINKS</h4>
  <ul class="abs" style="left:518px;top:122px">
    <li>Home</li><li>Book Appointment Online</li><li>Our Process</li><li>Photos</li><li>Testimonials</li><li>Blog</li>
  </ul>
  <div class="abs news" style="left:811px;top:50px">
    <h4>NEWSLETTER</h4>
    <p style="margin-top:22px">Register your email for<br>news for Bright Harbor</p>
    <input type="text" placeholder="Enter the email" style="margin-top:18px">
    <div class="submit" style="margin-top:28px">Submit</div>
  </div>
  <div class="abs copy">Copyright © 2018 Bright Harbor. All Rights Reserved.</div>
</footer>

</body>
</html>
```